Business Card Design Project

Business Card
We are rebranding with a new logo
Industry/Entity Type
Business
Contact Information for Business Card
Dennis Morvale +61 487215963 dennis@quorv.com.au P.O. Box 872 Fernlow QLD 4309
Requirements
Must have
- Logo

```html
<!DOCTYPE html>
<html lang="en">
<head>
<meta charset="utf-8">
<title>Quorv International – Business Card</title>
<link rel="stylesheet" href="https://fonts.googleapis.com/css2?family=Lato:wght@400;700&display=swap">
<style>
  :root {
    --backdrop: #3a3b3d;
    --card: #eef4f1;
    --block: #050505;
    --ink: #1b1b1b;
    --accent-orange: #e8731f;
    --accent-blue: #1f9ad6;
    --rule: #9fc9df;
  }
  * { box-sizing: border-box; margin: 0; padding: 0; }
  html, body {
    width: 1200px;
    height: 926px;
    overflow: hidden;
    background: var(--backdrop);
  }
  .stage {
    position: relative;
    width: 1200px;
    height: 926px;
  }
  .card {
    position: absolute;
    left: 100px;
    top: 177px;
    width: 1000px;
    height: 572px;
    background: var(--card);
    font-family: "Lato", sans-serif;
    color: var(--ink);
    box-shadow: 0 10px 30px rgba(0,0,0,.35);
  }
  .card__texture {
    position: absolute;
    inset: 0;
    background: radial-gradient(ellipse at 50% 50%, #f1f7f4 0%, #e7efeb 100%);
  }
  .brand-block {
    position: absolute;
    left: 0;
    top: 140px;
    width: 390px;
    height: 262px;
    background: var(--block);
    display: flex;
    flex-direction: column;
    justify-content: center;
    align-items: center;
  }
  .brand-block__name {
    font-weight: 700;
    font-size: 44px;
    letter-spacing: 3px;
    color: var(--accent-blue);
    line-height: 1.15;
    text-align: center;
  }
  .brand-block__name span { display: block; font-size: 22px; letter-spacing: 5px; }
  .holder {
    position: absolute;
    left: 448px;
    top: 188px;
  }
  .holder__name {
    font-size: 38px;
    font-weight: 400;
    letter-spacing: 1px;
    text-transform: uppercase;
  }
  .holder__name strong { font-weight: 700; }
  .holder__rule {
    width: 440px;
    height: 1px;
    background: var(--rule);
    margin: 14px 0 16px;
  }
  .contact-list { list-style: none; }
  .contact-list li {
    font-size: 26px;
    line-height: 38px;
    letter-spacing: .5px;
  }
  .contact-list .label {
    color: var(--accent-orange);
    font-weight: 700;
    margin-right: 6px;
  }
</style>
</head>
<body>
<div class="stage">
  <div class="card">
    <div class="card__texture" role="img" aria-label="Faint pale floral pattern across the card surface"></div>
    <div class="brand-block">
      <div class="brand-block__name">QUORV<span>INTERNATIONAL</span></div>
    </div>
    <div class="holder">
      <h1 class="holder__name">Dennis <strong>Morvale</strong></h1>
      <div class="holder__rule"></div>
      <ul class="contact-list">
        <li><span class="label">T.</span>+61 487215963</li>
        <li><span class="label">E.</span>dennis@quorv.com.au</li>
        <li><span class="label">A.</span>P.O. Box 872 Fernlow QLD 4309</li>
      </ul>
    </div>
  </div>
</div>
</body>
</html>
```